BuildLinkHub.com Full Stationery Design

Business Card will have all info on it. Letterhead will not have name, title or mobile number. Keep general feeling very clean, using colors from the logo as accents.
Name:Dale Marchetti
Title:President
Phone: 1-800-555-0142
Cell: 306-555-0187
email: dale@buildlinkhub.example
website: www.buildlinkhub.example
Address:
PO Box 947
Cedarvale, KR
S0J2T0

Target Market(s)

Construction Business owners

Industry/Entity Type

Business

Contact Information for Business Card

Name:Dale Marchetti
Title:President
Phone: 1-800-555-0142
Cell: 306-555-0187
Address:
PO Box 947
Cedarvale, KR
S0J2T0

Font styles to use
Sans Serif

Requirements
Must have
• Clean look
Should not have
• Images or cartoon type characters or tools

```html
<!DOCTYPE html>
<html lang="en">
<head>
<meta charset="UTF-8">
<title>BuildLinkHub.com Letterhead</title>
<link rel="stylesheet" href="https://fonts.googleapis.com/css2?family=Open+Sans:wght@400;600&display=swap">
<style>
  :root {
    --backdrop: #efe9e7;
    --paper: #ffffff;
    --brand-orange: #e9541c;
    --brand-orange-deep: #d9361a;
    --brand-slate: #5c6670;
    --rule-grey: #d6d8db;
    --text-grey: #5a6068;
  }
  * { margin: 0; padding: 0; box-sizing: border-box; }
  html, body {
    width: 1200px; height: 784px; overflow: hidden;
    background: var(--backdrop);
    font-family: "Open Sans", Arial, sans-serif;
  }
  .letterhead {
    position: absolute;
    left: 314px; top: 22px;
    width: 572px; height: 740px;
    background: var(--paper);
    box-shadow: 0 6px 22px rgba(80, 50, 45, 0.18);
    overflow: hidden;
  }
  .edge-mark {
    position: absolute;
    display: flex; flex-direction: column;
  }
  .edge-mark span { display: block; width: 4px; height: 14px; }
  .edge-mark .slate { background: var(--brand-slate); opacity: .7; }
  .edge-mark .orange { background: var(--brand-orange); }
  .edge-mark--left { left: 0; top: 26px; }
  .edge-mark--right { right: 0; top: 26px; }
  .brand {
    position: absolute; top: 96px; right: 52px;
    display: flex; align-items: center; gap: 8px;
  }
  .brand-dot { width: 16px; height: 16px; background: var(--brand-orange); }
  .brand-name {
    font-size: 17px; font-weight: 600; color: var(--brand-slate);
    letter-spacing: .2px;
  }
  .footer-wave { position: absolute; left: 0; bottom: 0; width: 572px; height: 300px; }
  .contact {
    position: absolute; left: 250px; bottom: 82px; width: 230px;
    color: var(--text-grey); font-size: 7.5px; line-height: 1.5;
  }
  .contact-rule {
    position: relative; height: 1px; background: var(--brand-slate);
    margin-bottom: 9px;
  }
  .contact-social {
    position: absolute; left: 50%; top: -4px; transform: translateX(-50%);
    display: flex; gap: 5px; background: var(--paper); padding: 0 4px;
  }
  .contact-social i { width: 8px; height: 8px; border-radius: 50%; background: var(--brand-orange); display: block; }
  .contact p { white-space: nowrap; }
  .sep { color: var(--brand-orange); padding: 0 2px; }
</style>
</head>
<body>
  <main class="letterhead">
    <div class="edge-mark edge-mark--left"><span class="slate"></span><span class="orange"></span></div>
    <div class="edge-mark edge-mark--right"><span class="slate"></span><span class="orange"></span></div>

    <header class="brand">
      <span class="brand-dot"></span>
      <span class="brand-name">BuildLinkHub.com</span>
    </header>

    <svg class="footer-wave" viewBox="0 0 572 300" preserveAspectRatio="none" aria-hidden="true">
      <defs>
        <linearGradient id="waveOrange" x1="0" y1="0" x2="1" y2="0">
          <stop offset="0" stop-color="#d9361a"/>
          <stop offset="1" stop-color="#e9541c"/>
        </linearGradient>
      </defs>
      <path d="M0 272 C 90 284, 150 240, 260 230 C 380 220, 440 262, 572 246" fill="none" stroke="#d6d8db" stroke-width="4"/>
      <path d="M0 286 C 90 292, 160 252, 270 244 C 390 236, 450 276, 572 256 L 572 300 L 0 300 Z" fill="url(#waveOrange)"/>
    </svg>

    <footer class="contact">
      <div class="contact-rule">
        <div class="contact-social"><i></i><i></i><i></i><i></i></div>
      </div>
      <p>PO Box 947, Cedarvale, KR S0J2T0<span class="sep">|</span>1-800-555-0142</p>
      <p>dale@buildlinkhub.example<span class="sep">|</span>www.buildlinkhub.example</p>
    </footer>
  </main>
</body>
</html>
```